ULMIRA card Technical Architecture

Hello everyone ULMIRA: It is a consulting firm in Architecture and Construction. I require a card duplexing, sober, elegant, classic but not boring. Update 1: Use the following data for the card. Name: Gonzalo Pereda Mauricio Villalta Position: COO Twitter: @ulmiraAT Homepage: ulmira-example.com home address not include the participation of all thank you.

Target Market(s)

Construction companies, Architects and Consulting Engineers

Industry/Entity Type

Consulting

Contact Information for Business Card

Los campos que debe tener:
Nombre, Cargo, email, homepage y twitter

Font styles to use
Serif
Sans Serif
Other font styles liked:
• Me gustan playfair display, open sans y roboto, pero estoy sujeto a sus propuestas

Requirements
Must have
• Colors: Present combined proposals in white, red, gray and black Update 1: The two names must be clearly differentiated from the two surnames
Nice to have
• They are free to present their best proposals. I will bring them immediate feedback to the extent you can go see their designs. Complete data for card and logo files will give the winner the

```html
<!DOCTYPE html>
<html lang="es">
<head>
<meta charset="utf-8">
<title>ULMIRA – Tarjetas de presentación</title>
<link href="https://fonts.googleapis.com/css2?family=Arimo:wght@400;700&display=swap" rel="stylesheet">
<style>
  :root {
    --backdrop: #3a3532;
    --card-black: #141414;
    --card-edge: #1d1d1d;
    --silver: #a9a9a9;
    --silver-dim: #7d7d7d;
    --brand-red: #b5121b;
    --text-white: #f2f2f2;
    --divider: #8a8a8a;
  }
  * { box-sizing: border-box; margin: 0; padding: 0; }
  html, body {
    width: 1200px; height: 864px; overflow: hidden;
    background: var(--backdrop);
    font-family: "Arimo", Arial, sans-serif;
  }
  .canvas { position: relative; width: 1200px; height: 864px; }
  .card {
    position: absolute;
    width: 520px; height: 300px;
    background: var(--card-black);
    border: 1px solid var(--card-edge);
    box-shadow: 0 18px 40px rgba(0,0,0,.45);
  }
  /* Front side */
  .card--front { left: 60px; top: 110px; }
  .front-brand {
    position: absolute; left: 70px; top: 92px;
    display: flex; align-items: center; gap: 16px;
  }
  .front-brand__name {
    font-size: 52px; font-weight: 400; letter-spacing: 22px;
    color: var(--silver);
  }
  .front-brand__square { width: 26px; height: 26px; background: var(--silver); }
  .front-rule {
    position: absolute; left: 70px; top: 160px; width: 380px; height: 1px;
    background: var(--silver-dim);
  }
  .front-tagline {
    position: absolute; left: 70px; top: 170px;
    font-size: 16px; letter-spacing: 4.2px; color: var(--silver-dim);
  }
  .front-web {
    position: absolute; left: 70px; top: 222px;
    font-size: 15px; letter-spacing: 4px; color: var(--silver);
  }
  /* Back side */
  .card--back { left: 620px; top: 420px; }
  .back-brand {
    position: absolute; left: 40px; top: 132px;
    display: flex; align-items: center; gap: 10px;
  }
  .back-brand__square { width: 18px; height: 18px; background: var(--brand-red); }
  .back-brand__name {
    font-size: 30px; font-weight: 700; letter-spacing: 3px; color: var(--brand-red);
  }
  .back-divider {
    position: absolute; left: 232px; top: 60px; width: 1px; height: 180px;
    background: var(--divider);
  }
  .contact { position: absolute; left: 256px; top: 74px; }
  .contact__name {
    font-size: 19px; font-weight: 700; line-height: 21px; color: var(--brand-red);
  }
  .contact__role { font-size: 16px; color: var(--text-white); margin-top: 4px; }
  .contact__list { list-style: none; margin-top: 14px; }
  .contact__item {
    display: flex; align-items: center; gap: 9px;
    font-size: 14px; line-height: 22px; color: var(--text-white);
  }
  .contact__icon { width: 13px; height: 13px; flex: none; }
</style>
</head>
<body>
<main class="canvas">
  <section class="card card--front" aria-label="Anverso de la tarjeta">
    <div class="front-brand">
      <span class="front-brand__name">ULMIRA</span>
      <span class="front-brand__square"></span>
    </div>
    <div class="front-rule"></div>
    <p class="front-tagline">ARQUITECTURA TÉCNICA</p>
    <p class="front-web">www.ulmira-example.com</p>
  </section>

  <section class="card card--back" aria-label="Reverso de la tarjeta">
    <div class="back-brand">
      <span class="back-brand__square"></span>
      <span class="back-brand__name">ULMIRA</span>
    </div>
    <div class="back-divider"></div>
    <div class="contact">
      <p class="contact__name">Mauricio Gonzalo<br>Pereda Villalta</p>
      <p class="contact__role">Director de Operaciones</p>
      <ul class="contact__list">
        <li class="contact__item">
          <svg class="contact__icon" viewBox="0 0 16 16" aria-hidden="true">
            <path fill="#b5121b" d="M3.5 1.5l2.5 0 1 3.5-1.7 1.2c.8 1.7 2.2 3.1 3.9 3.9L10.4 8.4l3.5 1v2.6c0 .8-.7 1.5-1.5 1.5C6.6 13.5 2 8.9 2 3c0-.8.7-1.5 1.5-1.5z"/>
          </svg>
          (+571) 555 010 2030
        </li>
        <li class="contact__item">
          <svg class="contact__icon" viewBox="0 0 16 16" aria-hidden="true">
            <circle cx="8" cy="8" r="6.5" fill="#b5121b"/>
          </svg>
          @ulmiraAT
        </li>
        <li class="contact__item">
          <svg class="contact__icon" viewBox="0 0 16 16" aria-hidden="true">
            <circle cx="8" cy="8" r="6.5" fill="none" stroke="#b5121b" stroke-width="1.5"/>
            <ellipse cx="8" cy="8" rx="2.8" ry="6.5" fill="none" stroke="#b5121b" stroke-width="1.2"/>
            <line x1="1.5" y1="8" x2="14.5" y2="8" stroke="#b5121b" stroke-width="1.2"/>
          </svg>
          www.ulmira-example.com
        </li>
      </ul>
    </div>
  </section>
</main>
</body>
</html>
```